Recto Verso Audiology Business Card

Business card with a beautiful design on the back. On the Recto you need the following data Lindqvist Oren Audiologist Hearing Solutions Hearing Protection Tinnitus Hyperacusis Tel: 0482/37 59 08 Email: On the back, you need something nice like the attached file. The logo "Corra Luna" can be in the center The colors of the Logo can not be changed If possible stay in the same colors as the logo Another solution is to put the logo on the front and have a nice back (A mosaic of small ears, hearing aids or other ..) Thank you _______________________________________________________________ Visit card On the Recto Lindqvist Oren Audiologist Hearing Solutions Hearing Protection Tinnitus Hyperacusis Tel: 0482/37 59 08 Email: You can put the logo " Corra Luna "on the Recto of the Verso The colors of the logo can not be changed. If you put the logo on the back, it must be well integrated. On the Verso I need something in the files. something stylish. It's a visit card for an audiologist. You can get ears of hearing aids if you need. Thanks

Target Market(s)

customers

Contact Information for Business Card

Carte de visite standard ou A6

Font styles to use
Serif
Sans Serif

Colors
33a6d7

Requirements
Must have
• the logo and a stylized background.
Nice to have
• It would be nice to have a back side related to audiology (ears, hearing aids etc.)

```html
<!DOCTYPE html>
<html lang="en">
<head>
<meta charset="utf-8">
<title>Corra Luna Audiology Business Card</title>
<link rel="stylesheet" href="https://fonts.googleapis.com/css2?family=Roboto:wght@400;500;700&display=swap">
<style>
  :root {
    --stage: #e9e9e7;
    --card: #232323;
    --card-deep: #1c1d1e;
    --pattern-tone: #23363a;
    --accent: #33a6d7;
    --accent-soft: #3bb8c4;
    --muted: #6f7b80;
    --ink-light: #f2f2f2;
  }
  * { box-sizing: border-box; margin: 0; padding: 0; }
  html, body { width: 1200px; height: 419px; overflow: hidden; }
  body {
    background: var(--stage);
    font-family: "Roboto", Arial, sans-serif;
    position: relative;
  }
  .card {
    position: absolute;
    top: 72px;
    width: 440px;
    height: 275px;
    border-radius: 4px;
    box-shadow: 0 6px 18px rgba(0,0,0,.25);
    overflow: hidden;
  }
  .card--front { left: 100px; }
  .card--back { left: 660px; background: var(--card); }

  .front-pattern {
    position: absolute; inset: 0;
    background: radial-gradient(circle at 50% 50%, var(--pattern-tone) 0%, var(--card-deep) 85%);
  }
  .brand {
    position: absolute;
    left: 50%; top: 50%;
    transform: translate(-50%, -50%);
    display: flex; align-items: center; gap: 12px;
    background: var(--card-deep);
    padding: 14px 18px;
  }
  .brand__mark {
    width: 14px; height: 14px;
    background: var(--accent-soft);
  }
  .brand__name {
    color: var(--accent-soft);
    font-weight: 500;
    font-size: 19px;
    line-height: 1.2;
    letter-spacing: 1px;
    text-transform: uppercase;
  }

  .holder {
    position: absolute; right: 28px; top: 92px;
    text-align: right;
  }
  .holder__name {
    color: var(--accent-soft);
    font-weight: 700;
    font-size: 17px;
    letter-spacing: .5px;
    text-transform: uppercase;
  }
  .holder__role {
    color: var(--muted);
    font-size: 13px;
    margin-top: 2px;
  }
  .contact {
    position: absolute; left: 28px; top: 148px;
    color: var(--ink-light);
    font-size: 12.5px;
    line-height: 1.5;
  }
  .services {
    color: var(--accent-soft);
    font-size: 12.5px;
    line-height: 1.4;
    margin-top: 4px;
  }
</style>
</head>
<body>
  <section class="card card--front" aria-label="Card front">
    <div class="front-pattern" role="img" aria-label="Repeating pattern of small ears and sound waves in teal on charcoal"></div>
    <div class="brand">
      <span class="brand__mark"></span>
      <span class="brand__name">Medical Center<br>Corra Luna</span>
    </div>
  </section>

  <section class="card card--back" aria-label="Card back">
    <div class="holder">
      <p class="holder__name">Lindqvist Oren</p>
      <p class="holder__role">Audiologist Hearing</p>
    </div>
    <div class="contact">
      <p>&nbsp;P : 0482/37 59 08</p>
      <p>hello@corraluna.be</p>
      <p>www.corraluna.be</p>
      <p class="services">Solutions Hearing<br>Protection| Tinnitus | Hyperacusis</p>
    </div>
  </section>
</body>
</html>
```